Elegant, Playful ReDesign of Paperlynx Website in wordpress - Budget has been raised

Project Brief: Paperlynx Website Redesign in WordPress

Introduction: Paperlynx, a cutting-edge document creation solution, aims to revolutionize the tedious process of crafting contracts, offers, forms, and other documents. By saving customers valuable time, streamlining workflows, and minimizing human error, Paperlynx has become an essential tool. As a technology company with a diverse clientele, we're set to boost our online presence through a refreshed WordPress website. Beyond a modernized website, we aspire to establish a stronger brand identity, incorporating graphic elements seamlessly into our online presence.

Current Status: Currently hosted on WordPress, Paperlynx's existing website serves its purpose but is ready for a visual transformation. Our goal is to maintain a modern and attractive appearance while upholding our commitment to simplicity and efficiency. Notably, the website is currently only in Danish. The redesigned structure should include a language switch function to cater to future international customers.

Objectives:
• Modern Aesthetic: Redesign the website with a fresh and modern vibe, reflecting innovation in the document creation sphere.
• User-Friendly: Prioritize an intuitive design for seamless navigation, ensuring visitors easily understand our offerings and benefits.
• Informative Content: Strike a balance between attractiveness and informativeness, clearly communicating Paperlynx's value proposition and simplifying business processes.
• Graphic Elements: Integrate visually appealing graphics that enhance the site's aesthetics and contribute to our overall visual identity. These elements should be versatile for future use in social media, advertisements, and other branding materials.
• Brand Recognition: Maintain our current logo and color scheme while exploring creative ways to establish a distinctive brand identity. The website should be a cornerstone for a cohesive branding strategy.
• Media Integration: Include images or videos on the website to enhance engagement. Find suitable, free-to-use visuals.
• Responsiveness: Ensure the design is responsive and works seamlessly on all devices.
• Demo Booking Form: Improve the design of the form to book a demo.
• Multilingual Support: Enable language transformation; the website is currently in Danish but should cater to other countries.

Guidelines:
• Typography: Up to the designer's discretion.
• Images/Videos: Must be free to use without additional charges.
• WordPress Theme: Use any WordPress theme below $100.
• Logo Redesign: Not needed; stick to the referenced color palette, as our new logo uses these colors.
• Color Palette: Stick to the existing company colors for consistency:
RGB
• #000b3c
• #004c6c
• #319ac3
• Greytones and white are also allowed
• Creativity Encouraged: Embrace creativity within the color palette for the layout, visuals, and overall user experience.

Conclusion: The Paperlynx website redesign marks an exciting opportunity to enhance our online presence. Our goal is to achieve a balance between a modern, attractive design and a clear, informative representation of our innovative solutions. We envision the revamped website as the foundation for a compelling online brand presence, with versatile graphic elements resonating across various digital platforms.

Sections that the website must include: Space for customer logos, space for testimonials, Space and redesign for display of price structure and price comparison, sections for company details and other information.

Design should also include a redesign of the customer cases section.
Generally there should just be a redesign of all things that are on the website.

Link to current website: https://paperlynx.example/

Target Market(s)

+50 employees.

Industry/Entity Type

Document automation

Coding

Coded - Design and coding required

Number of Pages Required

5+ page

Colors
0054AA
0677BA
7BADD7
CADEEF
E8F1F8

Requirements
Must have
• The new webpage must have the same pages as the current one. Frontpage, Book demo, About us, Case stories and Pricing

```html
<!DOCTYPE html>
<html lang="en">
<head>
<meta charset="utf-8">
<title>Paperlynx – Create Error-free Contracts and Quotes Quickly</title>
<link href="https://fonts.googleapis.com/css2?family=Roboto:wght@300;400;500;700;900&family=Roboto+Condensed:wght@400;700&display=swap" rel="stylesheet">
<style>
:root{
  --ink:#000b3c;
  --navy:#0c2f4f;
  --navy-deep:#082440;
  --teal:#004c6c;
  --sky:#319ac3;
  --brand:#1f6fa3;
  --card-grey:#e6e6e6;
  --card-mint:#d3e6ea;
  --text:#333a44;
  --muted:#6b7480;
  --white:#fff;
}
*{box-sizing:border-box;margin:0;padding:0}
html,body{width:1200px;height:4827px;overflow:hidden;background:#fff}
body{font-family:"Roboto",sans-serif;color:var(--text);position:relative}
.sec{position:absolute;left:0;width:1200px}
.abs{position:absolute}
.btn{display:inline-block;background:var(--sky);color:#fff;font-size:14px;font-weight:500;letter-spacing:.5px;padding:11px 32px;text-transform:uppercase}
.btn-outline{display:inline-block;border:1.5px solid var(--brand);color:var(--brand);font-size:10px;padding:5px 12px;letter-spacing:.4px;text-transform:uppercase}
.on-dark .btn-outline{border-color:#fff;color:#fff}

/* header */
.site-header{top:0;height:88px;background:#fff}
.logo{display:flex;align-items:center;gap:10px;font-size:24px;font-weight:700;color:var(--teal)}
.logo-mark{width:28px;height:28px;background:var(--sky)}
.site-header .logo{left:84px;top:28px}
.main-nav{right:70px;top:32px;display:flex;gap:18px;align-items:center;font-size:11px;color:var(--ink)}
.main-nav .current{border:1.5px solid var(--ink);padding:4px 10px}
.main-nav .login{background:var(--sky);color:#fff;padding:5px 14px}

/* hero */
.hero{top:88px;height:442px;background:linear-gradient(100deg,#17314f 0%,#2e4d6e 40%,#25415f 65%,#3a5673 100%)}
.hero h1{top:88px;left:0;width:1180px;text-align:center;color:#fff;font-size:44px;font-weight:700;line-height:52px}
.hero-points{top:225px;left:208px;display:grid;grid-template-columns:445px 330px;row-gap:8px;color:#fff;font-size:17px;list-style:none}
.hero .btn{top:382px;left:537px}

/* features */
.features{top:530px;height:203px;background:var(--navy)}
.feature{top:26px;width:320px;text-align:center;color:#fff}
.feature svg{display:block;margin:0 auto 14px}
.feature h3{font-size:14px;font-weight:500;text-transform:uppercase;margin-bottom:6px}
.feature p{font-size:11px;line-height:14px;color:#d7e2ec;width:260px;margin:0 auto}

/* clients */
.clients{top:733px;height:281px}
.sec-title{font-family:"Roboto Condensed",sans-serif;font-weight:700;color:var(--brand);font-size:31px;text-align:center;width:1200px;left:0}
.client{font-size:22px;font-weight:700;color:#3b3f45;width:180px;text-align:center}

/* testimonials */
.testimonials{top:1014px;height:480px}
.quote-card{top:127px;width:417px;height:196px;background:var(--card-grey);border-radius:10px;padding:52px 40px 0;text-align:center;font-size:11px;line-height:15px;color:#555}
.quote-card p+p{margin-top:12px}
.quote-badge{top:-17px;left:190px;width:36px;height:36px;border-radius:50%;background:var(--brand);color:#fff;font-size:26px;font-weight:900;line-height:44px;text-align:center}
.person{top:343px;display:flex;align-items:center;gap:14px}
.avatar{width:66px;height:66px;border-radius:50%;background:linear-gradient(135deg,#8a7a6a,#4a4540)}
.person b{display:block;font-size:15px;color:var(--ink);font-weight:500}
.person span{font-size:11px;color:var(--muted)}
.dots{top:431px;left:530px;display:flex;gap:16px}
.dots i{width:9px;height:9px;border-radius:50%;background:#c9c9c9}
.dots i:first-child{background:#666}

/* solution */
.solution{top:1494px;height:627px;background:linear-gradient(110deg,#1a3350 0%,#34506d 45%,#243f5d 100%);color:#fff}
.solution h2{top:34px;width:1200px;text-align:center;font-size:32px;line-height:37px;font-weight:700}
.solution .lead{top:146px;left:270px;width:660px;text-align:center;font-size:11px;line-height:18px}
.solution .lead2{top:196px;width:1200px;text-align:center;font-size:11px}
.step{top:277px;width:316px;height:258px;background:rgba(255,255,255,.12);border:1px solid rgba(255,255,255,.35)}
.step-screen{position:absolute;left:18px;top:10px;right:18px;bottom:10px;background:#f6f7f9}
.step-screen i{position:absolute;display:block;height:3px;background:#c9ced6}
.step-cap{top:560px;width:316px;text-align:center;font-size:17px;font-weight:500}

/* sign section */
.sign{top:2121px;height:700px}
.sign-heading{left:85px;top:36px;font-family:"Roboto Condensed",sans-serif;font-weight:700;font-size:27px;color:var(--brand)}
.sign-brand{left:85px;top:70px;font-size:54px;font-weight:700;color:var(--ink);letter-spacing:2px}
.sign-copy{left:85px;top:152px;width:430px;font-size:11px;line-height:15px;color:#444}
.video{background:linear-gradient(180deg,#2a2d35,#15171c)}
.player-bar{position:absolute;left:0;right:0;bottom:0;height:28px;background:rgba(0,0,0,.55)}
.player-bar::before{content:"";position:absolute;left:16px;top:8px;border-left:11px solid #fff;border-top:6px solid transparent;border-bottom:6px solid transparent}
.player-bar::after{content:"";position:absolute;left:40px;right:20px;top:2px;height:3px;background:#777}
.info-card{top:392px;left:126px;width:440px;height:276px;background:var(--card-mint);border-radius:16px;padding:28px 34px;font-size:11px;line-height:14px;color:#444}
.info-card h3,.plain-card h3{font-size:17px;font-weight:500;color:var(--ink);margin-bottom:8px}
.info-card p,.plain-card p{margin-bottom:10px}
.plain-card{top:392px;left:625px;width:400px;padding:28px 0;font-size:11px;line-height:14px;color:#444}

/* integration */
.integration{top:2513px;height:1119px;background:var(--navy);color:#fff}
.integration h2{left:702px;top:404px;font-family:"Roboto Condensed",sans-serif;font-weight:700;font-size:28px;line-height:34px}
.partner-box{left:702px;top:452px;width:415px;height:60px;background:#fff;display:flex;align-items:center;justify-content:space-around;color:var(--teal);font-size:24px;font-weight:700}
.int-copy{left:702px;top:540px;width:420px;font-size:11px;line-height:15px;color:#dfe7ef}
.col{top:752px;width:330px;font-size:11px;line-height:14px;color:#d9e3ec}
.col h3{font-size:17px;font-weight:500;color:#fff;margin-bottom:10px}
.col p{margin-bottom:10px}
.col-card{background:#1d466b;border-radius:12px;padding:22px 26px;top:752px;height:284px;width:360px}

/* demo */
.demo{top:3632px;height:288px;background:linear-gradient(100deg,#0e2a47 0%,#2a4a6b 50%,#173553 100%);color:#fff;text-align:center}
.demo h2{top:46px;width:1200px;font-size:32px;font-weight:700}
.demo p{top:108px;left:380px;width:440px;font-size:11px;line-height:16px}
.demo .btn{top:200px;left:480px;background:var(--teal);padding:12px 26px}

/* mobile */
.mobile{top:3920px;height:507px}
.mobile h2{left:87px;top:62px;font-family:"Roboto Condensed",sans-serif;font-weight:700;font-size:31px;color:var(--brand)}
.mobile-copy{left:87px;top:128px;width:480px;font-size:12px;line-height:15px;color:#444}
.mobile-copy p{margin-bottom:15px}
.mobile .btn{left:87px;top:368px;background:var(--teal);padding:11px 30px}

/* footer */
.site-footer{top:4427px;height:400px;background:var(--navy-deep);color:#fff}
.footer-logo{left:82px;top:35px;width:255px;height:72px;background:#fff;display:flex;align-items:center;justify-content:center}
.footer-contact{left:82px;top:140px;font-size:12px;line-height:19px}
.follow{left:82px;top:202px;font-size:11px}
.socials{left:82px;top:224px;display:flex;gap:10px}
.socials i{width:20px;height:20px;border-radius:50%;background:#fff}
.footer-nav{left:490px;top:135px;font-size:11px;line-height:22px;text-transform:uppercase;list-style:none}
.meet{left:772px;top:135px;width:300px;font-size:12px;line-height:17px}
.meet b{display:block;font-size:14px;font-weight:500;margin-bottom:6px}
.copyright{top:345px;width:1200px;text-align:center;font-size:9px;color:#aab7c5}
</style>
</head>
<body>

<header class="sec site-header">
  <div class="abs logo"><span class="logo-mark"></span>Paperlynx</div>
  <nav class="abs main-nav">
    <span class="current">Home</span><span>Customer Cases</span><span>Video</span><span>Live Demo</span><span>Prices</span><span>About Us</span><span class="login">Login</span><span>English ▾</span>
  </nav>
</header>

<section class="sec hero" role="img" aria-label="Photo of business people reviewing documents and a calculator, in blue tones">
  <h1 class="abs">Create Error-free Contracts<br>and Quotes Quickly</h1>
  <ul class="abs hero-points">
    <li>· Get Paragraphs Inserted Automatically</li><li>· Get Prices Calculated Automatically</li>
    <li>· Eliminate Manual Work</li><li>·Sign Digitally</li>
  </ul>
  <span class="abs btn">Get Started</span>
</section>

<section class="sec features">
  <div class="abs feature" style="left:83px">
    <svg width="44" height="44" viewBox="0 0 44 44" fill="none" stroke="#319ac3" stroke-width="2"><circle cx="22" cy="22" r="18"/><circle cx="22" cy="22" r="12"/><path d="M22 14v8l5 4"/></svg>
    <h3>Save Time</h3><p>Reduce your time consumption by up to 90% when creating customer contracts and offers.</p>
  </div>
  <div class="abs feature" style="left:409px">
    <svg width="44" height="44" viewBox="0 0 44 44" fill="none" stroke="#319ac3" stroke-width="2"><circle cx="22" cy="22" r="18"/><circle cx="22" cy="22" r="12"/><path d="M16 22l4 4 8-8"/></svg>
    <h3>High Quality</h3><p>Automation gives you minimal work and eliminates errors in your documents.</p>
  </div>
  <div class="abs feature" style="left:757px">
    <svg width="54" height="44" viewBox="0 0 54 44" fill="none" stroke="#319ac3" stroke-width="2"><rect x="6" y="4" width="16" height="10" rx="2"/><rect x="32" y="16" width="16" height="10" rx="2"/><rect x="6" y="30" width="16" height="10" rx="2"/><path d="M22 9h6v12h4M22 35h6V21"/></svg>
    <h3>Streamlined Flow</h3><p>Be guided all the way through the document and ask for review before sending the document for digital signature.</p>
  </div>
</section>

<section class="sec clients">
  <h2 class="abs sec-title" style="top:30px">1000+ Companies Trust</h2>
  <div class="abs client" style="left:110px;top:122px;font-size:15px">PLANFORGE</div>
  <div class="abs client" style="left:316px;top:118px">Kestrel Legal</div>
  <div class="abs client" style="left:510px;top:118px">Crateworks</div>
  <div class="abs client" style="left:700px;top:118px">Webtrove</div>
  <div class="abs client" style="left:898px;top:122px;font-size:15px">NEXA FILES</div>
  <div class="abs client" style="left:110px;top:208px;font-size:28px">Veltro</div>
  <div class="abs client" style="left:316px;top:208px">Brightpath</div>
  <div class="abs client" style="left:510px;top:212px;font-size:17px">CrmNova</div>
  <div class="abs client" style="left:700px;top:212px;font-size:15px">LUMEN LAW</div>
  <div class="abs client" style="left:898px;top:208px">Holtgaard</div>
</section>

<section class="sec testimonials">
  <h2 class="abs sec-title" style="top:26px">Appreciated And Recommended By</h2>
  <div class="abs quote-card" style="left:161px">
    <div class="abs quote-badge">“</div>
    <p>I didn't imagine our offer could be fully automated just like that, but we gave it a shot because I saw what others had done with Paperlynx.</p>
    <p>The result has become razor sharp – I am completely happy when I stand with a new offer in my hand.</p>
  </div>
  <div class="abs quote-card" style="left:650px">
    <div class="abs quote-badge">“</div>
    <p>We had been looking for a long time for the right platform to digitize our unique paragraph collection, and had no doubts after trying Paperlynx's solution.</p>
    <p>It places high demands on the solution when complex paradigms are to be digitized, and we did not want to compromise on either quality or the experience.</p>
  </div>
  <div class="abs person" style="left:168px"><div class="avatar" role="img" aria-label="Portrait photo"></div><div><b>Jonas Holm Lindberg</b><span>Sales director – Harbor Security</span></div></div>
  <div class="abs person" style="left:660px"><div class="avatar" role="img" aria-label="Portrait photo"></div><div><b>Mikkel Dahl Sørensen</b><span>Manager – Nexa Files</span></div></div>
  <div class="abs dots"><i></i><i></i><i></i><i></i></div>
</section>

<section class="sec solution" role="img" aria-label="Photo of a person working on a laptop with charts, in dark blue tones">
  <h2 class="abs">Intelligent Document<br>Solution</h2>
  <p class="abs lead">Leave the creation of your documents to our intelligent solution. It can automatically calculate your prices and insert the sections that need to be included in your documents. Get rid of manual work with legal uncertainties and become more efficient.</p>
  <p class="abs lead2">Choose one of your automated documents, fill in the question frame and sign digitally – it's that simple!</p>
  <div class="abs step" style="left:80px"><div class="step-screen">
    <i style="left:14px;top:16px;width:80px"></i><i style="left:14px;top:40px;width:210px"></i><i style="left:14px;top:56px;width:210px"></i><i style="left:14px;top:72px;width:210px"></i><i style="left:14px;top:88px;width:210px"></i><i style="left:14px;top:104px;width:210px"></i><i style="left:14px;top:120px;width:210px"></i><i style="left:14px;top:150px;width:60px"></i><i style="left:14px;top:170px;width:210px"></i><i style="left:14px;top:186px;width:210px"></i><i style="left:14px;top:202px;width:210px"></i>
    <svg class="abs" style="left:110px;top:90px" width="60" height="60" viewBox="0 0 60 60" stroke="#222" stroke-width="4" fill="none"><path d="M4 20V4h16M40 4h16v16M56 40v16H40M20 56H4V40M4 4l20 20M56 4 36 24M56 56 36 36M4 56l20-20"/></svg>
  </div></div>
  <div class="abs step" style="left:438px"><div class="step-screen">
    <i style="left:14px;top:14px;width:60px"></i><i style="left:14px;top:28px;width:220px"></i><i style="left:14px;top:42px;width:150px;background:#9fd19f"></i><i style="left:14px;top:70px;width:90px"></i><i style="left:14px;top:90px;width:50px"></i><i style="left:14px;top:110px;width:220px"></i><i style="left:14px;top:130px;width:50px"></i><i style="left:14px;top:150px;width:100px"></i><i style="left:130px;top:150px;width:100px"></i><i style="left:14px;top:180px;width:70px"></i>
  </div></div>
  <div class="abs step" style="left:797px"><div class="step-screen" style="background:#2b2f36">
    <div class="abs" style="left:14px;top:14px;right:14px;bottom:14px;background:#fff"><i style="left:20px;top:100px;width:70px"></i><i style="left:20px;top:116px;width:50px"></i><i style="left:170px;top:100px;width:40px"></i></div>
    <div class="abs" style="right:4px;top:140px;width:8px;height:60px;background:#3cb55a"></div>
  </div></div>
  <div class="abs step-cap" style="left:80px">1. Select document</div>
  <div class="abs step-cap" style="left:438px">2. Complete guided flow</div>
  <div class="abs step-cap" style="left:797px">3. Sign digitally</div>
</section>

<section class="sec integration on-dark">
  <div class="abs video" style="left:75px;top:397px;width:532px;height:305px;background:linear-gradient(180deg,#eef0f3,#cfd4db);border:8px solid #2c3138" role="img" aria-label="Video: Paperlynx module for the CRM integration">
    <div class="abs" style="left:0;right:0;top:0;height:34px;background:rgba(40,44,52,.85)"></div>
    <div class="player-bar"></div>
  </div>
  <h2 class="abs">Integration To Crm</h2>
  <div class="abs partner-box"><span>CrmNova</span><span>Webtrove</span></div>
  <p class="abs int-copy">Create your offers or customer contracts directly in your CRM solution, and send them for digital signature with a few clicks. Experience better insight and timing in your sales with an integration to CrmNova. The integration has been created in collaboration with Webtrove.</p>
  <div class="abs col" style="left:94px">
    <h3>Digital signature</h3>
    <p>Send your automated documents for digital signature or upload your digital signature. Send your offers for digital signature with data directly from your CRM solution – quickly and easily.</p>
    <p>Keep an eye on how far the customer is in the process, the signature process and get status updated in CRM the solution along the way.</p>
    <p>Get your offers signed more often and faster with a digital signature.</p>
    <span class="btn-outline">Read more</span>
  </div>
  <div class="abs col col-card" style="left:419px">
    <h3>Automated offers</h3>
    <p>Create error-free offers with data from your CRM solution using a guided flow and avoid manual errors.</p>
    <p>Get tailored your offers down to the smallest detail and get sections all relevant sections and calculate your prices automatically.</p>
    <p>Send the offer for digital signature and get the status updated along the way in the CRM solution.</p>
    <span class="btn-outline">Read more</span>
  </div>
  <div class="abs col" style="left:820px">
    <h3>Leads from your Website</h3>
    <p>Manage your leads and customer inquiries with intelligent forms directly on your own website.</p>
    <p>Give your lead an estimate price or offer draft immediately, which you can work on from your CRM solution.</p>
    <p>Get created leads automatically in your CRM solution for easy follow up.</p>
    <span class="btn-outline">Read more</span>
  </div>
</section>

<section class="sec sign">
  <svg class="abs" style="left:0;top:0" width="1200" height="720" viewBox="0 0 1200 720"><path d="M0 0H1200V480C1200 590 1150 720 1020 720H150Q0 720 0 560Z" fill="#fff"/></svg>
  <div class="abs sign-heading">Sign With</div>
  <div class="abs sign-brand">INKSURE</div>
  <p class="abs sign-copy">Send your documents for signature with one of the Nordics' leading and most secure digital signature solutions. Inksure has, for example, been accepted on the EU's trusted list, which only few providers and the Danish state has achieved in Denmark.</p>
  <div class="abs video" style="left:575px;top:78px;width:519px;height:286px" role="img" aria-label="Video: Digital signature and document flow overview">
    <svg class="abs" style="left:20px;top:50px" width="480" height="200" viewBox="0 0 480 200">
      <g fill="none" stroke="#ddd" stroke-width="2"><rect x="2" y="8" width="12" height="12"/><rect x="2" y="58" width="12" height="12"/><rect x="2" y="108" width="12" height="12"/><rect x="2" y="158" width="12" height="12"/></g>
      <g fill="#3cb55a"><rect x="40" y="8" width="160" height="12"/><rect x="40" y="58" width="160" height="12"/><rect x="40" y="108" width="160" height="12"/><rect x="40" y="158" width="160" height="12"/></g>
      <g fill="#d94141"><rect x="340" y="6" width="50" height="16"/><rect x="340" y="56" width="50" height="16"/></g>
      <g fill="#e6e6e6"><rect x="340" y="106" width="50" height="16"/><rect x="340" y="156" width="50" height="16"/><circle cx="440" cy="14" r="10"/><circle cx="440" cy="64" r="10"/><circle cx="440" cy="114" r="10"/><circle cx="440" cy="164" r="10"/></g>
    </svg>
    <div class="player-bar"></div>
  </div>
  <div class="abs info-card">
    <h3>Digital signature</h3>
    <p>Send your automated documents for digital signature or upload your own with a few clicks – quickly and easily.</p>
    <p>The solution automatically sends reminders about signatures, and you can keep an eye on how far the signer is in the signature process along the way.</p>
    <p>Get your offers signed more often and faster with a digital signature for the benefit of both yourself and the signatories.</p>
    <span class="btn-outline" style="border-color:#444;color:#444">Read more</span>
  </div>
  <div class="abs plain-card">
    <h3>Mass broadcast</h3>
    <p>Send the same document for signature by many different signers at once or personalize the document with merged information.</p>
    <p>You can also ask the user for input before a document is created and signed.</p>
    <p>Start your mass broadcast and wait for the solution to automatically collect signatures from hundreds or thousands of users.</p>
    <span class="btn-outline">Read more</span>
  </div>
</section>

<section class="sec demo" role="img" aria-label="Photo of a laptop with a video play button, in dark blue tones">
  <h2 class="abs">START LIVE DEMO</h2>
  <p class="abs">Experience the intuitive and intelligent flow for creating documents on your own. In a few minutes you have a complete document – ready for digital signature.</p>
  <span class="abs btn">Start Live Demo</span>
</section>

<section class="sec mobile">
  <h2 class="abs">Activate Your Mobile</h2>
  <div class="abs mobile-copy">
    <p>Create your documents when it suits you. They can be created on any device and signed much faster.</p>
    <p>Select document<br>Complete the question frame<br>Sign digitally</p>
    <p>For example, create an offer on a mobile or a tablet while talking to a potential customer at a meeting. Get approval instantly and send it for digital signature before you go home.</p>
  </div>
  <span class="abs btn">Get Started</span>
  <div class="abs" style="left:629px;top:56px;width:480px;height:380px;background:linear-gradient(135deg,#e9f1f8,#cadeef)" role="img" aria-label="Illustration of people using the Paperlynx app on a phone and a tablet"></div>
</section>

<footer class="sec site-footer">
  <div class="abs footer-logo"><div class="logo"><span class="logo-mark"></span>Paperlynx</div></div>
  <div class="abs footer-contact">Mail: contact@paperlynx.example<br>Phone: +45 12 34 56 78<br>Address: Linde Allé 14, 2750 Nordby</div>
  <div class="abs follow">Follow us on</div>
  <div class="abs socials"><i></i><i></i><i></i><i></i></div>
  <ul class="abs footer-nav"><li>Home</li><li>Customer Review</li><li>Video Demo</li><li>Prices</li><li>About Us</li></ul>
  <div class="abs meet"><b>Meet Us Online</b>We Would Love To Link And Share Thoughts And Ideas. Follow Us And Stay Updated On The Latest News.</div>
  <div class="abs copyright">Copyright © 2024 Paperlynx. All rights reserved.</div>
</footer>

</body>
</html>
```